FernPath....... a dash of Glow

I need a web design for a new business based in London that will be mobile (offered at homes, parks or a local cafe ect) called FernPath. I offer Life Coaching/Counselling sessions, Personal training, Massage and Sports Massage. Sessions range from an hour to half and hour. My aim is to help people along their journey to help give them gain clarity of where there going, helping them to towards their goals, so that can experience bliss. My website should represent a place people can come to release their stress and worries so that they leave feeling lighter, clearer and happier. I would like my website to reflect someone feeling ALIVE. I would also like a logo design for FernPath with a sentence underneath or near saying A dash of Glow.

Target Market(s)

middle class people

Industry/Entity Type

Business

Coding

Coded - Design and coding required

Number of Pages Required

4 page

Requirements
Must have
• 1st page About us
• 2nd page Services
• 3rd page Prices
• 4th page contact details
Nice to have
• mixture of cultures in images

```html
<!DOCTYPE html>
<html lang="en">
<head>
<meta charset="utf-8">
<title>FernPath — A dash of Glow</title>
<link rel="stylesheet" href="https://fonts.googleapis.com/css2?family=Dancing+Script:wght@500;600&family=Raleway:wght@300;400;500&display=swap">
<style>
:root{
  --teal:#35b8a6;
  --teal-dark:#2aa593;
  --gold:#d8a63c;
  --gold-text:#d4a53e;
  --ink:#333;
  --muted:#555;
  --white:#fff;
  --line:#cfe9e5;
}
*{margin:0;padding:0;box-sizing:border-box}
html,body{width:933px;height:1200px;overflow:hidden}
body{font-family:"Raleway",sans-serif;color:var(--ink);background:var(--white);position:relative}
.abs{position:absolute}

/* header */
.site-header{position:absolute;left:0;top:0;width:933px;height:110px;background:var(--white)}
.topbar{position:absolute;left:250px;top:0;width:683px;height:38px}
.topbar-items{position:absolute;left:370px;top:0;height:38px;display:flex;align-items:center;color:var(--white);font-size:13px}
.social-dots{position:absolute;left:382px;top:13px;display:flex;gap:14px}
.social-dots span{width:11px;height:11px;border-radius:50%;background:var(--white)}
.top-email{position:absolute;left:510px;top:11px;color:var(--white);font-size:13px;display:flex;align-items:center;gap:7px}
.top-phone{position:absolute;left:728px;top:11px;color:var(--white);font-size:13px;display:flex;align-items:center;gap:7px}
.brand{position:absolute;left:92px;top:30px;text-align:center}
.brand-row{display:flex;align-items:center;gap:6px}
.brand-dot{width:12px;height:12px;border-radius:50%;background:var(--teal)}
.brand-name{font-size:26px;font-weight:500;color:var(--teal);letter-spacing:.5px}
.brand-tag{font-size:8px;color:var(--ink);margin-top:4px}
.main-nav{position:absolute;top:70px;left:0;font-size:11px;letter-spacing:.3px}
.main-nav a{position:absolute;white-space:nowrap;color:#222;text-decoration:none}
.main-nav a.is-active{color:var(--teal)}

/* hero */
.hero{position:absolute;left:0;top:110px;width:933px;height:462px;
  background:radial-gradient(ellipse at 72% 45%,#fffbe6 0%,#fbe4a0 22%,#f3c56a 48%,#e6a947 75%,#cf8d3a 100%)}
.hero-figure{position:absolute;left:470px;top:20px;width:230px;height:442px;
  background:linear-gradient(180deg,rgba(60,35,20,.55),rgba(40,25,15,.8));border-radius:110px 110px 20px 20px;opacity:.55}
.hero-title{position:absolute;left:116px;top:178px}
.hero-script{font-family:"Dancing Script",cursive;font-size:40px;color:#2e2a26;font-weight:500}
.hero-word{font-size:58px;font-weight:300;color:var(--teal);line-height:1;letter-spacing:2px}
.slider-dots{position:absolute;left:410px;top:432px;display:flex;gap:16px}
.slider-dots span{width:9px;height:9px;border-radius:50%;border:1.5px solid #333}
.slider-dots span.on{background:var(--teal);border-color:var(--teal)}

/* contact */
.contact{position:absolute;left:0;top:572px;width:933px;height:349px;
  background:linear-gradient(180deg,#fff 0%,#f6f6f6 45%,#f3f3f3 100%)}
.contact-photo{position:absolute;left:290px;top:100px;width:260px;height:249px;border-radius:130px 130px 0 0;
  background:linear-gradient(180deg,rgba(210,210,210,.45),rgba(235,235,235,.2))}
.section-title{position:absolute;left:0;width:933px;top:40px;text-align:center;font-family:"Dancing Script",cursive;font-size:38px;color:var(--gold-text);font-weight:500}
.section-title em{font-style:normal;color:var(--teal);font-size:28px;margin-left:8px}
.divider{position:absolute;left:368px;top:96px}
.contact-label{position:absolute;top:203px;font-size:11px;color:var(--muted)}
.contact-value{position:absolute;top:236px;font-size:18px;color:#444;display:flex;align-items:center;gap:12px;white-space:nowrap}
.vrule{position:absolute;top:232px;width:1px;height:28px;background:var(--line)}
.follow-dot{position:absolute;top:241px;width:12px;height:12px;border-radius:50%;background:var(--teal)}

/* footer */
.site-footer{position:absolute;left:0;top:921px;width:933px;height:279px;background:var(--gold);color:var(--white)}
.footer-brand{position:absolute;left:100px;top:70px;width:104px;text-align:center}
.footer-brand .brand-name{color:var(--white);font-size:28px}
.footer-brand .brand-dot{background:var(--white)}
.footer-copy{position:absolute;left:100px;top:188px;width:104px;text-align:center;font-size:10.5px;line-height:15px}
.footer-heading{position:absolute;font-family:"Dancing Script",cursive;font-size:24px;font-weight:500;color:#5a4320}
.footer-social{position:absolute;left:304px;top:94px;display:flex;gap:25px}
.footer-social span{width:12px;height:12px;border-radius:50%;background:var(--white)}
.timing{position:absolute;left:303px;top:175px;font-size:11px;line-height:19px}
.timing td{padding:0}
.timing td:nth-child(2){padding:0 12px 0 12px}
.footer-list{position:absolute;list-style:none;font-size:11px}
.footer-list li{height:28.4px;position:relative;padding-left:13px}
.footer-list li::before{content:"";position:absolute;left:0;top:4px;width:4px;height:4px;border-right:1px solid #fff;border-top:1px solid #fff;transform:rotate(45deg)}
.footer-list li.cont::before{display:none}
</style>
</head>
<body>

<header class="site-header">
  <svg class="topbar" width="683" height="38" viewBox="0 0 683 38" aria-hidden="true">
    <path d="M0 0 H683 V38 H110 C60 38 30 20 0 0 Z" fill="var(--teal)"/>
  </svg>
  <div class="social-dots"><span></span><span></span><span></span></div>
  <div class="top-email">
    <svg width="13" height="10" viewBox="0 0 13 10"><rect width="13" height="10" rx="1" fill="#fff"/><path d="M0 1 L6.5 6 L13 1" stroke="var(--teal)" stroke-width="1.3" fill="none"/></svg>
    hello@fernpath.co
  </div>
  <div class="top-phone">
    <svg width="13" height="13" viewBox="0 0 24 24"><path fill="#fff" d="M6.6 10.8a15.1 15.1 0 006.6 6.6l2.2-2.2a1 1 0 011-.25 11.4 11.4 0 003.6.57 1 1 0 011 1V20a1 1 0 01-1 1A17 17 0 013 4a1 1 0 011-1h3.5a1 1 0 011 1c0 1.25.2 2.45.57 3.57a1 1 0 01-.25 1z"/></svg>
    (800) 555-0142
  </div>

  <div class="brand">
    <div class="brand-row"><span class="brand-dot"></span><span class="brand-name">FernPath</span></div>
    <div class="brand-tag">A dash of Glow</div>
  </div>

  <nav class="main-nav">
    <a class="is-active" style="left:385px">HOME</a>
    <a style="left:473px">ABOUT US</a>
    <a style="left:584px">SERVICES</a>
    <a style="left:694px">PRICES</a>
    <a style="left:790px">CONTACT</a>
  </nav>
</header>

<section class="hero">
  <div class="abs" role="img" aria-label="Photo of a woman with arms outstretched on a beach at golden sunset" style="inset:0"></div>
  <div class="hero-figure" aria-hidden="true"></div>
  <div class="hero-title">
    <div class="hero-script">A dash of</div>
    <div class="hero-word">GLOW</div>
  </div>
  <div class="slider-dots"><span></span><span></span><span class="on"></span><span></span><span></span></div>
</section>

<section class="contact">
  <div class="contact-photo" role="img" aria-label="Faint photo of a woman looking up, smiling"></div>
  <h2 class="section-title">Contact<em>us</em></h2>
  <svg class="divider" width="196" height="12" viewBox="0 0 196 12" aria-hidden="true">
    <line x1="10" y1="6" x2="186" y2="6" stroke="var(--gold-text)" stroke-width="1.2"/>
    <circle cx="6" cy="6" r="2.5" fill="none" stroke="var(--gold-text)"/>
    <circle cx="190" cy="6" r="2.5" fill="none" stroke="var(--gold-text)"/>
  </svg>

  <div class="contact-label" style="left:74px">Phone</div>
  <div class="contact-label" style="left:342px">Email</div>
  <div class="contact-label" style="left:709px">Follow us</div>

  <div class="contact-value" style="left:74px">
    <svg width="14" height="14" viewBox="0 0 24 24"><path fill="var(--teal)" d="M6.6 10.8a15.1 15.1 0 006.6 6.6l2.2-2.2a1 1 0 011-.25 11.4 11.4 0 003.6.57 1 1 0 011 1V20a1 1 0 01-1 1A17 17 0 013 4a1 1 0 011-1h3.5a1 1 0 011 1c0 1.25.2 2.45.57 3.57a1 1 0 01-.25 1z"/></svg>
    0 700 555 0193
  </div>
  <div class="vrule" style="left:268px"></div>
  <div class="contact-value" style="left:305px">
    <svg width="15" height="11" viewBox="0 0 13 10"><rect width="13" height="10" rx="1" fill="var(--teal)"/><path d="M0 1 L6.5 6 L13 1" stroke="#fff" stroke-width="1.3" fill="none"/></svg>
    fernpath.adashofglow@mailbox.co
  </div>
  <div class="vrule" style="left:671px"></div>
  <span class="follow-dot" style="left:706px"></span>
  <div class="vrule" style="left:751px"></div>
  <span class="follow-dot" style="left:783px"></span>
  <div class="vrule" style="left:828px"></div>
  <span class="follow-dot" style="left:857px"></span>
</section>

<footer class="site-footer">
  <div class="footer-brand">
    <div class="brand-row" style="justify-content:center"><span class="brand-dot"></span></div>
    <div class="brand-name" style="margin-top:8px">FernPath</div>
  </div>
  <div class="footer-copy">© 2015<br>Allrights Reserved</div>

  <div class="footer-heading" style="left:303px;top:48px">Follow us</div>
  <div class="footer-social"><span></span><span></span><span></span></div>

  <div class="footer-heading" style="left:303px;top:138px">Timing</div>
  <table class="timing">
    <tr><td>Mon - Fri</td><td>:</td><td>6:00am - 11:00pm</td></tr>
    <tr><td>Sat</td><td>:</td><td>7:00am - 10:00pm</td></tr>
    <tr><td>Sun</td><td>:</td><td>Closed</td></tr>
  </table>

  <div class="footer-heading" style="left:540px;top:48px">Navigation</div>
  <ul class="footer-list" style="left:541px;top:99px">
    <li>About</li><li>Classes</li><li>Gallery</li><li>Testimonials</li><li>Contact us</li>
  </ul>

  <div class="footer-heading" style="left:710px;top:48px">Services</div>
  <ul class="footer-list" style="left:711px;top:99px">
    <li>Life / personal Performance</li><li class="cont">Coaching</li><li>Angel Readings</li><li>Personal training</li><li>Sports Massage &amp; Massage</li>
  </ul>
</footer>

</body>
</html>
```